BRIGHT RIVER POWER.

I'd like my business logo.
contact name: Dennis Halvorsen
phone:0438759164
email: info@brightriverpower.net.au
website: www.brightriverpower.net.au

services:
solar
battery storage
LED lighting
energy saving solutions
general electrical
I'd like the design to look professional

Target Market(s)

Everyone

Industry/Entity Type

Business

Contact Information for Business Card

as described above

Requirements
Must have
• Id like the colours and the design to work well with my logo.

```html
<!DOCTYPE html>
<html lang="en">
<head>
<meta charset="utf-8">
<title>Bright River Power – Business Card</title>
<link href="https://fonts.googleapis.com/css2?family=Open+Sans:wght@400;600;700&display=swap" rel="stylesheet">
<style>
  :root {
    --backdrop: #3b3633;
    --card-black: #111111;
    --card-green: #4aa63a;
    --brand-green: #5cb83f;
    --text-white: #ffffff;
    --icon-orange: #f2a51f;
  }
  * { margin: 0; padding: 0; box-sizing: border-box; }
  html, body {
    width: 1200px; height: 900px; overflow: hidden;
    background: var(--backdrop);
    font-family: "Open Sans", Arial, sans-serif;
  }
  .stage {
    position: relative; width: 1200px; height: 900px;
    display: flex; align-items: center; justify-content: center; gap: 40px;
  }
  .card {
    width: 525px; height: 300px; border-radius: 4px;
    box-shadow: 0 12px 30px rgba(0,0,0,.45);
    position: relative; overflow: hidden;
  }
  /* Front */
  .card-front {
    background: var(--card-black);
    display: flex; flex-direction: column; align-items: center;
    padding-top: 46px;
  }
  .brand {
    display: flex; align-items: center; gap: 14px;
  }
  .brand-dot {
    width: 40px; height: 40px; border-radius: 50%;
    background: var(--brand-green);
  }
  .brand-name {
    font-weight: 700; font-size: 30px; letter-spacing: 1px;
    color: var(--brand-green);
  }
  .contact-name {
    margin-top: 34px;
    font-weight: 700; font-size: 20px; letter-spacing: .5px;
    color: var(--brand-green); text-transform: uppercase;
  }
  .contact-icons { display: flex; gap: 8px; margin-top: 10px; }
  .contact-icons svg { width: 12px; height: 12px; }
  .contact-lines {
    list-style: none; margin-top: 6px; text-align: center;
    color: var(--text-white); font-size: 15px; line-height: 22px;
  }
  /* Back */
  .card-back {
    background: var(--card-green);
    display: flex; align-items: center; padding: 0 40px 0 44px; gap: 36px;
  }
  .back-mark {
    display: flex; flex-direction: column; align-items: center; gap: 12px;
    width: 170px;
  }
  .back-mark-dot {
    width: 90px; height: 90px; border-radius: 50%; background: var(--text-white);
  }
  .back-mark-name {
    font-weight: 700; font-size: 15px; color: var(--text-white);
    text-align: center; letter-spacing: 1px;
  }
  .services-title {
    font-weight: 700; font-size: 19px; color: var(--text-white);
    margin-bottom: 10px;
  }
  .services-list {
    list-style: none; color: var(--text-white); font-size: 15px; line-height: 22px;
  }
  .services-list li::before {
    content: ""; display: inline-block; width: 7px; height: 7px;
    border-radius: 50%; background: var(--text-white);
    margin-right: 10px; vertical-align: middle;
  }
</style>
</head>
<body>
  <main class="stage">
    <section class="card card-front">
      <div class="brand">
        <span class="brand-dot"></span>
        <span class="brand-name">BRIGHT RIVER POWER</span>
      </div>
      <p class="contact-name">Dennis Halvorsen</p>
      <div class="contact-icons" aria-hidden="true">
        <svg viewBox="0 0 12 12"><path d="M2 1h3l1 3-2 1a7 7 0 0 0 3 3l1-2 3 1v3c-6 0-10-4-10-9z" fill="var(--icon-orange)"/></svg>
        <svg viewBox="0 0 12 12"><rect x="0.5" y="2.5" width="11" height="7" fill="var(--icon-orange)"/><path d="M0.5 2.5 6 7l5.5-4.5" stroke="#111" fill="none"/></svg>
        <svg viewBox="0 0 12 12"><circle cx="6" cy="6" r="5.5" fill="var(--icon-orange)"/><path d="M0.5 6h11M6 0.5c-3 3-3 8 0 11M6 0.5c3 3 3 8 0 11" stroke="#111" fill="none" stroke-width=".8"/></svg>
      </div>
      <ul class="contact-lines">
        <li>0438759164</li>
        <li>info@brightriverpower.net.au</li>
        <li>www.brightriverpower.net.au</li>
      </ul>
    </section>

    <section class="card card-back">
      <div class="back-mark">
        <span class="back-mark-dot"></span>
        <span class="back-mark-name">BRIGHT RIVER POWER</span>
      </div>
      <div class="services">
        <h2 class="services-title">WHAT I DO</h2>
        <ul class="services-list">
          <li>Solar</li>
          <li>Battery Storage</li>
          <li>LED Lighting</li>
          <li>Energy Saving Solutions</li>
        </ul>
      </div>
    </section>
  </main>
</body>
</html>
```